RTavenor Business Cards & Letterhead

I have a logo but need a design for some new business cards. We are a Design-Build Firm that specializes in the design and construction of commercial projects.
the cards need to be professional. no cartoon stuff.
i would like to have the cards in AI format so I can update the card as needed. Logo is provided.
Our Address is: 4187 Marlowe Ct. Apex, North Carolina 27614

```html
<!DOCTYPE html>
<html lang="en">
<head>
<meta charset="utf-8">
<title>RTavenor Business Card</title>
<link href="https://fonts.googleapis.com/css2?family=Open+Sans:wght@400;600;800&display=swap" rel="stylesheet">
<style>
  :root {
    --page-bg: #e9e9eb;
    --card-dark: #222328;
    --brand-blue: #1a78c2;
    --band-blue-start: #1c7cc4;
    --band-blue-end: #0d4d82;
    --logo-grey: #6e7076;
    --text-white: #f2f3f5;
    --divider: #5a5c62;
    --back-center: #1879bd;
    --back-edge: #0b3c63;
    --back-mark: #0c4774;
  }
  * { margin: 0; padding: 0; box-sizing: border-box; }
  html, body { width: 1200px; height: 780px; overflow: hidden; }
  body {
    background: var(--page-bg);
    font-family: "Open Sans", Arial, sans-serif;
    display: flex;
    align-items: center;
    justify-content: center;
    gap: 40px;
  }
  .card {
    position: relative;
    width: 540px;
    height: 309px;
    overflow: hidden;
    box-shadow: 0 6px 18px rgba(0,0,0,0.18);
  }
  .card-front { background: var(--card-dark); }
  .brand {
    position: absolute;
    top: 42px;
    left: 170px;
    display: flex;
    align-items: center;
    gap: 10px;
  }
  .brand-square {
    width: 30px; height: 30px;
    background: var(--brand-blue);
  }
  .brand-name {
    font-weight: 800;
    font-size: 44px;
    letter-spacing: 1px;
    color: var(--logo-grey);
    text-transform: uppercase;
    line-height: 1;
  }
  .identity {
    position: absolute;
    top: 150px;
    left: 36px;
  }
  .person-name {
    font-weight: 600;
    font-size: 22px;
    color: var(--brand-blue);
    text-transform: uppercase;
    letter-spacing: 0.5px;
  }
  .person-title {
    margin-top: 4px;
    margin-left: 40px;
    font-size: 14px;
    color: var(--text-white);
  }
  .divider {
    position: absolute;
    top: 138px;
    left: 258px;
    width: 1px;
    height: 80px;
    background: var(--divider);
  }
  .contact {
    position: absolute;
    top: 146px;
    left: 280px;
    list-style: none;
  }
  .contact li {
    display: flex;
    align-items: center;
    gap: 8px;
    font-size: 15px;
    color: var(--text-white);
    line-height: 22px;
  }
  .contact svg { width: 13px; height: 13px; flex: none; }
  .address-band {
    position: absolute;
    left: 0; right: 0;
    top: 236px;
    height: 34px;
    background: linear-gradient(90deg, var(--band-blue-start), var(--band-blue-end));
    display: flex;
    align-items: center;
    padding-left: 36px;
    font-size: 15px;
    color: var(--text-white);
  }
  .card-back {
    background: radial-gradient(ellipse at 50% 50%, var(--back-center) 0%, var(--back-edge) 80%);
    display: flex;
    align-items: center;
    justify-content: center;
  }
  .back-mark {
    display: flex;
    align-items: center;
    gap: 10px;
  }
  .back-mark .brand-square { background: var(--back-mark); }
  .back-mark .brand-name { color: var(--back-mark); }
</style>
</head>
<body>
  <section class="card card-front">
    <div class="brand">
      <span class="brand-square"></span>
      <span class="brand-name">RTavenor</span>
    </div>

    <div class="identity">
      <p class="person-name">Owen Tavenor</p>
      <p class="person-title">Founder/President</p>
    </div>

    <span class="divider"></span>

    <ul class="contact">
      <li>
        <svg viewBox="0 0 16 16" aria-hidden="true"><circle cx="8" cy="8" r="8" fill="#1a78c2"/><path d="M5.2 4.2l1.4-.3.8 1.9-.9.7a5 5 0 0 0 2.4 2.4l.7-.9 1.9.8-.3 1.4c-3.4.3-6.3-2.6-6-6z" fill="#fff"/></svg>
        (919) 555-0148
      </li>
      <li>
        <svg viewBox="0 0 16 16" aria-hidden="true"><circle cx="8" cy="8" r="8" fill="#1a78c2"/><circle cx="8" cy="8" r="4.5" fill="none" stroke="#fff" stroke-width="1"/><path d="M3.5 8h9M8 3.5c-2 2.5-2 6.5 0 9M8 3.5c2 2.5 2 6.5 0 9" fill="none" stroke="#fff" stroke-width="1"/></svg>
        www.rtavenor.com
      </li>
      <li>
        <svg viewBox="0 0 16 16" aria-hidden="true"><circle cx="8" cy="8" r="8" fill="#1a78c2"/><rect x="4" y="5.2" width="8" height="5.6" fill="none" stroke="#fff" stroke-width="1"/><path d="M4 5.2l4 3 4-3" fill="none" stroke="#fff" stroke-width="1"/></svg>
        OTR@RTavenor.com
      </li>
    </ul>

    <div class="address-band">4187 Marlowe Ct. Apex, North Carolina 27614</div>
  </section>

  <section class="card card-back">
    <div class="back-mark">
      <span class="brand-square"></span>
      <span class="brand-name">RTavenor</span>
    </div>
  </section>
</body>
</html>
```